Austin TX First Veterinary Urgent Care

We need a flyer designed for us and our clinic that is eye-catching but also summarizes the advantages of our services. We want to express that we are family owned, have convenient hours and affordable prices. We are the first veterinary urgent care animal clinic in Austin Texas. Our hours of operation are M-F 12PM-9PM S-S 10AM-6PM. Our Address is 4871 W Larkspur Rd Suite B212 Austin, Tx 78753. Our phone number is (737)555-0148 our website is www.brookpawclinic.com and our email address is info@brookpawclinic.com.

Target Market(s)

Pet owners and veterinary professionals for referral purposes.

Industry/Entity Type

Veterinary

Font styles to use
Sans Serif

Colors
0094D4
00A9DD
6FCCEA
C7EBF8
E9F6FB
00AB8E
00BBA5
67D7C9
C6EFE9
E9F9F6

Requirements
Must have
• Our logo, hours of operation and contact information easy to read. Should emphasize that we are affordable as well as family owned. List of services should also be displayed: ear, eye, and skin issues, limping, broken toenails, lacerations, coughing, sneezing, allergies, vomiting and diarrhea, urinary issues, constipation, snake bites, toxin ingestion, and many many more
Nice to have
• We would like to have a modern feel with drawn/cartoon images, not realistic stock photos of dogs/cats.

```html
<!DOCTYPE html>
<html lang="en">
<head>
<meta charset="utf-8">
<title>BrookPaw Vet – Austin TX First Veterinary Urgent Care</title>
<link href="https://fonts.googleapis.com/css2?family=Poppins:wght@400;500;600;700;800&display=swap" rel="stylesheet">
<style>
  :root{
    --navy:#0c0a88;
    --green:#45ad55;
    --panel:#e3e2e5;
    --ink:#1d1d2b;
    --paper:#ffffff;
    --backdrop:#f1f1f3;
    --pet-dark:#6b3d2c;
    --pet-warm:#c9703a;
    --duo-purple:#c9b0ee;
    --duo-orange:#f59a3a;
  }
  *{box-sizing:border-box;margin:0;padding:0}
  html,body{width:1200px;height:2197px;overflow:hidden;background:var(--backdrop);font-family:"Poppins",sans-serif}
  .stage{position:relative;width:1200px;height:2197px}
  .flyer{position:absolute;left:50px;top:386px;width:947px;height:1227px;background:var(--paper);overflow:hidden;transform:scale(1.1616);transform-origin:top left;box-shadow:0 10px 30px rgba(0,0,0,.12)}
  .shapes{position:absolute;inset:0;width:947px;height:1227px}
  .abs{position:absolute}

  .brand{left:140px;top:62px;display:flex;align-items:center;gap:12px}
  .brand-dot{width:40px;height:40px;border-radius:50%;background:var(--green)}
  .brand-name{font-weight:800;font-size:36px;color:var(--navy);letter-spacing:-.5px}

  .headline{left:46px;top:140px;font-weight:800;line-height:1;color:var(--navy);text-transform:uppercase}
  .headline .l1{display:block;font-size:50px;letter-spacing:-.5px}
  .headline .l2{display:block;font-size:67px;color:var(--green);margin-top:2px;letter-spacing:-.5px}
  .headline .l3{display:block;font-size:61px;margin-top:2px;letter-spacing:-.5px}
  .intro{left:48px;top:326px;width:425px;font-size:14.5px;line-height:1.3;color:var(--ink)}

  .promise{left:100px;top:400px;width:414px;height:56px;background:var(--green);border-radius:0 28px 28px 0;padding:8px 20px 0 40px;color:#fff;font-weight:700;font-size:14px;line-height:1.4}
  .promise-badge{left:48px;top:392px;width:74px;height:74px;border-radius:50%;background:var(--navy);border:4px solid #fff}

  .pets-art{left:30px;top:490px;width:515px;height:345px;border-radius:28px;background:linear-gradient(120deg,var(--pet-dark) 0%,var(--pet-warm) 55%,#e3b79a 100%)}
  .duo-art{left:510px;top:0;width:437px;height:395px}

  .hours{left:48px;top:846px;width:480px}
  .hours-head{background:var(--green);color:#fff;font-weight:700;font-size:27px;height:64px;border-radius:28px 28px 0 0;padding:12px 0 0 34px;letter-spacing:-.2px}
  .hours-body{background:var(--navy);color:#fff;border-radius:0 0 30px 30px;padding:20px 34px 24px}
  .hours-row{display:flex;justify-content:space-between;font-weight:700;font-size:22px;padding:6px 0}
  .hours-row+.hours-row{border-top:2px solid #fff;margin-top:10px;padding-top:14px}

  .services{left:553px;top:413px;width:342px}
  .services-head{background:var(--navy);color:#fff;font-weight:700;font-size:28px;height:80px;border-radius:34px 34px 0 0;padding:24px 0 0 40px;letter-spacing:-.2px}
  .services-list{list-style:none;background:var(--panel);border-radius:0 0 44px 44px;padding:20px 0 52px 30px;height:568px}
  .services-list li{font-size:23px;color:var(--ink);line-height:35px;display:flex;align-items:center;gap:16px}
  .services-list li::before{content:"";width:14px;height:14px;border-radius:50%;background:var(--green);flex:none}

  .contact{left:48px;top:1094px;color:var(--ink);font-style:normal}
  .contact-row{display:flex;align-items:center;gap:10px;font-weight:700;margin-bottom:8px}
  .call-label{color:var(--green);font-size:20px;font-weight:700;margin-right:8px}
  .phone{font-size:20px}
  .detail{font-size:15px}
  .icon{width:30px;height:30px;flex:none}
  .gap{margin-left:10px}
</style>
</head>
<body>
<div class="stage">
  <div class="flyer">
    <svg class="shapes" viewBox="0 0 947 1227" aria-hidden="true">
      <path d="M0 0H265C235 40 180 25 150 60C115 100 70 120 0 130Z" fill="var(--navy)"/>
      <path d="M265 0C235 40 180 25 150 60C115 100 70 120 0 130" fill="none" stroke="var(--green)" stroke-width="5"/>
      <path d="M175 6C210 26 240 24 262 4" fill="none" stroke="var(--green)" stroke-width="5"/>
      <path d="M580 1227C590 1150 650 1090 760 1100C820 1105 860 1120 947 1100V1227Z" fill="var(--navy)"/>
      <path d="M540 1227C600 1165 700 1165 820 1160C900 1150 935 1060 947 920V1227Z" fill="var(--green)"/>
      <path d="M540 1227C600 1165 700 1165 820 1160C900 1150 935 1060 947 920" fill="none" stroke="var(--navy)" stroke-width="3"/>
    </svg>

    <svg class="abs duo-art" viewBox="0 0 437 395" role="img" aria-label="Cartoon illustration of a winking cat and a happy puppy in a green circle">
      <defs>
        <linearGradient id="duoFill" x1="0" y1="0" x2="1" y2="1">
          <stop offset="0" stop-color="var(--green)"/>
          <stop offset=".55" stop-color="var(--duo-purple)"/>
          <stop offset="1" stop-color="var(--duo-orange)"/>
        </linearGradient>
      </defs>
      <circle cx="220" cy="170" r="215" fill="url(#duoFill)" stroke="var(--navy)" stroke-width="4"/>
    </svg>

    <div class="abs brand">
      <span class="brand-dot"></span>
      <span class="brand-name">BrookPaw Vet</span>
    </div>

    <h1 class="abs headline">
      <span class="l1">Austin TX First</span>
      <span class="l2">Veterinary</span>
      <span class="l3">Urgent Care</span>
    </h1>
    <p class="abs intro">We are the first veterinary urgent care animal clinic in Austin Texas.</p>

    <div class="abs promise">WE ARE FAMILY OWNED, HAVE CONVENIENT<br>HOURS AND AFFORDABLE PRICES</div>
    <div class="abs promise-badge" role="img" aria-label="Family icon badge"></div>

    <div class="abs pets-art" role="img" aria-label="Cartoon illustration of four dogs sitting together"></div>

    <section class="abs hours">
      <h2 class="hours-head">OUR HOURS OF OPERATION</h2>
      <div class="hours-body">
        <div class="hours-row"><span>Monday to Friday</span><span>12PM-9PM</span></div>
        <div class="hours-row"><span>Saturday to Sunday</span><span>10AM-6PM</span></div>
      </div>
    </section>

    <section class="abs services">
      <h2 class="services-head">LIST OF SERVICES</h2>
      <ul class="services-list">
        <li>Ear</li>
        <li>Eye</li>
        <li>Skin issues</li>
        <li>Limping</li>
        <li>Broken toenails</li>
        <li>Lacerations</li>
        <li>Coughing</li>
        <li>Sneezing</li>
        <li>Allergies</li>
        <li>Vomiting &amp; Diarrhea</li>
        <li>Urinary issues</li>
        <li>Constipation</li>
        <li>Snake bites</li>
        <li>Toxin ingestion</li>
      </ul>
    </section>

    <address class="abs contact">
      <div class="contact-row">
        <span class="call-label">CALL US</span>
        <svg class="icon" viewBox="0 0 30 30" aria-hidden="true"><circle cx="15" cy="15" r="14" fill="var(--navy)"/><path d="M10 8l3 3-2 2c1 2 3 4 5 5l2-2 3 3-2 3c-5 0-11-6-11-11z" fill="#fff"/></svg>
        <span class="phone">(737)555-0148</span>
      </div>
      <div class="contact-row">
        <svg class="icon" viewBox="0 0 30 30" aria-hidden="true"><circle cx="15" cy="15" r="14" fill="var(--navy)"/><path d="M15 7a5 5 0 0 1 5 5c0 4-5 10-5 10s-5-6-5-10a5 5 0 0 1 5-5z" fill="#fff"/><circle cx="15" cy="12" r="2" fill="var(--navy)"/></svg>
        <span class="detail">4871 W Larkspur Rd Suite B212 Austin, Tx 78753</span>
      </div>
      <div class="contact-row">
        <svg class="icon" viewBox="0 0 30 30" aria-hidden="true"><circle cx="15" cy="15" r="14" fill="var(--navy)"/><rect x="8" y="10" width="14" height="10" rx="1" fill="#fff"/><path d="M8 11l7 5 7-5" fill="none" stroke="var(--navy)" stroke-width="1.5"/></svg>
        <span class="detail">info@brookpawclinic.com</span>
        <svg class="icon gap" viewBox="0 0 30 30" aria-hidden="true"><circle cx="15" cy="15" r="14" fill="var(--navy)"/><circle cx="15" cy="15" r="7" fill="none" stroke="#fff" stroke-width="1.5"/><path d="M8 15h14M15 8c-3 4-3 10 0 14M15 8c3 4 3 10 0 14" fill="none" stroke="#fff" stroke-width="1.3"/></svg>
        <span class="detail">www.brookpawclinic.com</span>
      </div>
    </address>
  </div>
</div>
</body>
</html>
```